Tech business card design

We need an amazing business card design for our new business 'Pexla' a marketing tech startup based in Sydney, Australia. We provide an online marketplace for businesses to search and buy advertising media, connect with service providers and learn more about marketing. We wish to communicate 'cool tech', reliability and professionalism and design based around our logo.

Target Market(s)

Business Owners

Contact Information for Business Card

Name
Position
Email Address
Website
Phone Number

Font styles to use
Other font styles liked:
• Avenir & Avenir Next

Colors

Designer to choose colors to be used in the design.

```html
<!DOCTYPE html>
<html lang="en">
<head>
<meta charset="utf-8">
<title>Pexla Business Card</title>
<link href="https://fonts.googleapis.com/css2?family=Source+Sans+3:wght@400;700&display=swap" rel="stylesheet">
<style>
  :root {
    --board: #a0cee2;
    --card: #ffffff;
    --ink: #13133a;
    --rule: #1c2250;
    --rule-soft: #2b3a78;
    --text: #3a3a3a;
  }
  * { margin: 0; padding: 0; box-sizing: border-box; }
  html, body {
    width: 1200px; height: 1184px; overflow: hidden;
    background: var(--board);
    font-family: "Source Sans 3", "Myriad Pro", sans-serif;
  }
  .card {
    position: absolute; left: 149px; width: 902px; height: 515px;
    background: var(--card);
  }
  .card--front { top: 43px; }
  .card--back { top: 629px; }
  .rule { position: absolute; height: 3px; background: var(--rule); }
  .card--back .rule { background: var(--rule-soft); }
  .wordmark {
    position: absolute; font-weight: 700; color: var(--ink);
    font-size: 132px; line-height: 1; letter-spacing: -2px;
  }
  .card--front .wordmark { left: 38px; top: 200px; }
  .card--back .wordmark { left: 0; width: 902px; text-align: center; top: 202px; }
  .holder { position: absolute; right: 73px; top: 181px; text-align: right; color: var(--ink); }
  .holder__name { font-weight: 700; font-size: 33px; line-height: 34px; }
  .holder__role { font-size: 28px; line-height: 30px; color: #222; }
  .address {
    position: absolute; right: 73px; top: 278px; text-align: right;
    font-size: 24px; line-height: 30px; color: var(--text);
  }
  .contacts { position: absolute; right: 73px; top: 360px; list-style: none; }
  .contacts li {
    display: flex; align-items: center; justify-content: flex-end;
    font-size: 24px; height: 33px; color: var(--text);
  }
  .contacts svg { width: 22px; height: 22px; margin-left: 14px; }
  .site {
    position: absolute; left: 0; width: 902px; top: 425px; text-align: center;
    font-size: 31px; letter-spacing: 4px; color: var(--text);
  }
</style>
</head>
<body>
  <section class="card card--front">
    <div class="rule" style="left:0;width:27px;top:256px"></div>
    <div class="rule" style="left:401px;width:501px;top:256px"></div>
    <div class="wordmark">pexla</div>
    <div class="holder">
      <p class="holder__name">JOHN SMITH</p>
      <p class="holder__role">Position</p>
    </div>
    <p class="address">Street name City Name,<br>Zipcode,012345</p>
    <ul class="contacts">
      <li>012-345-6789
        <svg viewBox="0 0 22 22" fill="none" stroke="#13133a" stroke-width="1.6"><circle cx="11" cy="11" r="9.5"/><path d="M8 6c-1.5 1-1.5 4 .5 7s4.5 4 6 3l-1.5-2-1.5.6c-1-.8-2-2.4-2.3-3.6l1.2-1L8 6z" fill="#13133a" stroke="none"/></svg>
      </li>
      <li>info@pexla.com
        <svg viewBox="0 0 22 22"><rect x="1" y="5" width="20" height="13" fill="#13133a"/><path d="M1 5l10 7 10-7M1 18l7-6M21 18l-7-6" stroke="#fff" stroke-width="1.4" fill="none"/></svg>
      </li>
      <li>www.pexla.com
        <svg viewBox="0 0 22 22" fill="none" stroke="#13133a" stroke-width="1.4"><circle cx="11" cy="11" r="9.5"/><ellipse cx="11" cy="11" rx="4" ry="9.5"/><path d="M1.5 11h19M3 6h16M3 16h16M11 1.5v19"/></svg>
      </li>
    </ul>
  </section>

  <section class="card card--back">
    <div class="rule" style="left:0;width:253px;top:255px"></div>
    <div class="rule" style="left:636px;width:266px;top:255px"></div>
    <div class="wordmark">pexla</div>
    <p class="site">www.pexla.com</p>
  </section>
</body>
</html>
```